Brand new letterhead, business card, email signature etc.

We are a financial company in London, UK. Our website is www.marlowvane.com. We're wanting a complete remodel of the company colours, letter head, business cards, email signatures, etc. Looking to keep the same font for the company name. I have upload a colour palette that we want to work with. We're looking for company letterhead for outgoing letters/ correspondence, letterhead for internal documentation, email signatures, e-letters. etc. Ultimately we will redesign the entire website also. It is important that our clients get a strong, secure, warm, trustworthy, solid feeling and first impression.
Updates

Designs look the same

Target Market(s)

Institutional investors, (ultra) high net worth individuals

Industry/Entity Type

Finance, Invesments banking.

Font styles to use
Other font styles liked:
• Current font is "Champagne & Limousines"

Requirements
Must have
• Must use the colours provided on the PDF uploaded to the portal. The purple = main colour. The red = accent colour.
Nice to have
• Nice to use same font as now for the company name "Corvane". Font is "Champagne & Limousines". Nice to have some reference to the old logo flower, but only subtle.
Should not have
• Do not use the colour red from our website. Use the colours provided on the colour palette PDF that I uploaded in the portal.

```html
<!DOCTYPE html>
<html lang="en">
<head>
<meta charset="utf-8">
<title>Corvane Letterhead</title>
<link href="https://fonts.googleapis.com/css2?family=Lato:wght@300;400;700&family=Dancing+Script:wght@600&display=swap" rel="stylesheet">
<style>
  :root {
    --backdrop: #e9e9ea;
    --paper: #ffffff;
    --ink: #1f1a1c;
    --ink-soft: #4a4345;
    --plum: #2e0f1c;
    --crimson: #c41a35;
  }
  * { box-sizing: border-box; margin: 0; padding: 0; }
  html, body {
    width: 1200px; height: 874px; overflow: hidden;
    background: var(--backdrop);
    font-family: "Lato", sans-serif;
    color: var(--ink);
  }
  .letterhead {
    position: absolute; left: 310px; top: 27px;
    width: 580px; height: 820px;
    background: var(--paper);
    box-shadow: 0 6px 22px rgba(0,0,0,0.12);
    overflow: hidden;
  }
  .brand {
    position: absolute; left: 40px; top: 58px;
    display: flex; align-items: center; gap: 16px;
  }
  .brand-square {
    width: 50px; height: 50px;
    border: 1.5px solid var(--plum);
  }
  .brand-name {
    font-weight: 300; font-size: 38px; letter-spacing: 12px;
    color: var(--plum); line-height: 1;
  }
  .contact {
    position: absolute; left: 392px; top: 36px;
    border-left: 1.5px solid var(--plum);
    padding-left: 12px;
    font-size: 8px; font-weight: 300; line-height: 1.45;
    color: var(--ink-soft);
  }
  .contact-row { display: flex; align-items: center; gap: 5px; }
  .contact-row svg { width: 7px; height: 7px; fill: var(--plum); }
  .contact-address { margin-top: 5px; }
  .letter {
    position: absolute; left: 40px; top: 150px; width: 490px;
    font-size: 11px; line-height: 1.4;
  }
  .date { margin-bottom: 10px; }
  .recipient { margin-bottom: 10px; }
  .salutation { font-weight: 700; font-size: 14px; margin-bottom: 10px; }
  .letter p.body { margin-bottom: 12px; }
  .closing { margin-top: 16px; }
  .signature {
    font-family: "Dancing Script", cursive;
    font-size: 30px; margin-top: 36px; color: var(--ink);
  }
  .footer-band {
    position: absolute; left: 0; bottom: 0; width: 580px; height: 22px;
  }
</style>
</head>
<body>
  <main class="letterhead">
    <header class="brand">
      <div class="brand-square"></div>
      <div class="brand-name">CORVANE</div>
    </header>

    <address class="contact" style="font-style:normal">
      <div class="contact-row">
        <svg viewBox="0 0 10 10"><path d="M2 0.5 L4 2.5 L3 4 Q4.5 6 6 7 L7.5 6 L9.5 8 L8 9.5 Q3 9 0.5 2 Z"/></svg>
        <span>020 7946 0318</span>
      </div>
      <div class="contact-row">
        <svg viewBox="0 0 10 10"><rect x="0" y="2" width="10" height="6.5"/></svg>
        <span>info@marlowvane.com</span>
      </div>
      <div class="contact-row">
        <svg viewBox="0 0 10 10"><circle cx="5" cy="5" r="4.5"/></svg>
        <span>www.marlowvane.com</span>
      </div>
      <div class="contact-address">
        Corvane Group Limited<br>
        9th Floor 14 Aldgate Row<br>
        London EC3N 2LP
      </div>
    </address>

    <section class="letter">
      <div class="date">January-03-2020</div>
      <div class="recipient">Mr. Arthur Penrose<br>President</div>
      <div class="recipient">Halden Trust<br>123 Street Name, Suite# 10<br>City, State, 120023</div>
      <div class="salutation">Dear Mr. Arthur</div>
      <p class="body">Lorem ipsum dolor sit amet, consectetur adipiscing elit, sed do eiusmod tempor incididunt ut labore et dolore magna aliqua. Ut enim ad minim veniam, quis nostrud exercitation ullamco laboris nisi ut aliquip ex ea commodo consequat. Duis aute irure dolor in reprehenderit in voluptate velit esse cillum dolore eu fugiat nulla pariatur.</p>
      <p class="body">Lorem ipsum dolor sit amet, consectetur adipiscing elit, sed do eiusmod tempor incididunt ut labore et dolore magna aliqua. Ut enim ad minim veniam, quis nostrud exercitation ullamco laboris nisi ut aliquip ex ea commodo consequat. Duis aute irure dolor in reprehenderit in voluptate velit esse cillum dolore eu fugiat nulla pariatur.</p>
      <p class="body">Lorem ipsum dolor sit amet, consectetur adipiscing elit, sed do eiusmod tempor incididunt ut labore et dolore magna aliqua. Ut enim ad minim veniam, quis nostrud exercitation ullamco laboris nisi ut aliquip ex ea commodo consequat.</p>
      <p class="body">Excepteur sint occaecat cupidatat non proident, sunt in culpa qui officia deserunt mollit anim id est laborum, re et dolore magnam aliquam quaerat voluptatem.</p>
      <div class="closing">Regards</div>
      <div class="signature">Elise Warren</div>
    </section>

    <svg class="footer-band" viewBox="0 0 580 22" preserveAspectRatio="none">
      <polygon points="0,0 350,0 340,22 0,22" fill="var(--plum)"/>
      <polygon points="354,14 580,14 580,22 350,22" fill="var(--crimson)"/>
    </svg>
  </main>
</body>
</html>
```